Business Card Design for Occupational Medicine Start Up Company

We need to design a professional business card. We are a healthcare company providing occupational medicine services to blue collar industries. We are professional, efficient and high quality service providers.

Target Market(s)

Blue Collar Industry: Shipbuilding, Ports, Trucking Companies; The Executives and Safety Officers for these companies

Industry/Entity Type

Healthcare

Contact Information for Business Card

Logo, Name, Title, Email, Phone

Other font styles liked:
• Please match our Brand Guide

Requirements
Must have
• Our Company Colors and Logo

```html
<!DOCTYPE html>
<html lang="en">
<head>
<meta charset="UTF-8">
<title>Harborline Clinics – Business Card</title>
<link href="https://fonts.googleapis.com/css2?family=Montserrat:wght@400;600;700&display=swap" rel="stylesheet">
<style>
  :root {
    --stage: #2a2a2a;
    --card-light: #ebebeb;
    --navy: #2b3586;
    --orange: #f7b347;
    --sky: #2aa6e0;
    --ink: #4a4a4a;
    --white: #ffffff;
  }
  * { margin: 0; padding: 0; box-sizing: border-box; }
  html, body { width: 1200px; height: 1107px; overflow: hidden; }
  body {
    background: var(--stage);
    font-family: "Montserrat", sans-serif;
    position: relative;
  }
  .card {
    position: absolute;
    left: 236px;
    width: 803px;
    height: 461px;
    overflow: hidden;
  }
  .card-front { top: 69px; background: var(--card-light); }
  .card-back { top: 579px; background: var(--navy); }

  /* Front */
  .front-brand {
    position: absolute;
    left: 90px; top: 300px;
    width: 300px;
    top: 296px;
    display: flex; align-items: center; gap: 10px;
    top: 290px;
  }
  .front-brand {
    top: 0; left: 0; width: 401px; height: 440px;
    justify-content: center;
  }
  .brand-dot {
    width: 22px; height: 22px; border-radius: 50%;
    background: var(--navy); flex: none;
  }
  .brand-name {
    font-weight: 700; font-size: 26px; letter-spacing: 1px;
    color: var(--navy);
  }
  .divider {
    position: absolute; left: 401px; top: 147px;
    width: 2px; height: 195px; background: var(--navy);
  }
  .contact {
    position: absolute; left: 483px; top: 146px;
    color: var(--ink);
  }
  .person-name { font-size: 25px; font-weight: 400; color: var(--navy); line-height: 1.2; }
  .person-name .surname { color: var(--orange); }
  .person-title { font-size: 16px; margin-top: 3px; }
  .contact-list { list-style: none; margin-top: 20px; }
  .contact-list li {
    display: flex; align-items: center; gap: 10px;
    font-size: 17px; height: 28px;
  }
  .contact-list svg { width: 16px; height: 16px; flex: none; }
  .web .accent { color: var(--orange); }
  .address { font-size: 17px; line-height: 26px; margin-top: 12px; }
  .front-stripe {
    position: absolute; left: 0; bottom: 0; height: 11px; width: 100%;
    display: flex;
  }
  .front-stripe .navy { width: 404px; background: var(--navy); }
  .front-stripe .orange { flex: 1; background: var(--orange); }

  /* Back */
  .back-brand {
    position: absolute; left: 0; top: 140px; width: 100%;
    text-align: center; color: var(--white);
  }
  .back-dot {
    width: 56px; height: 56px; border-radius: 50%;
    background: var(--white); margin: 0 auto 40px;
  }
  .back-name { font-size: 42px; font-weight: 700; letter-spacing: 0.5px; line-height: 1; }
  .back-sub { font-size: 21px; font-weight: 700; letter-spacing: 6px; margin-top: 8px; }
  .back-stripe { position: absolute; left: 0; width: 100%; }
  .back-stripe.orange { top: 415px; height: 8px; background: var(--orange); }
  .back-stripe.sky { top: 431px; height: 10px; background: var(--sky); }
</style>
</head>
<body>
  <section class="card card-front">
    <div class="front-brand">
      <span class="brand-dot"></span>
      <span class="brand-name">HARBORLINE</span>
    </div>
    <div class="divider"></div>
    <div class="contact">
      <p class="person-name">Nadia <span class="surname">Verel</span></p>
      <p class="person-title">Directeur</p>
      <ul class="contact-list">
        <li>
          <svg viewBox="0 0 16 16"><path fill="#2b3586" d="M3.5 1.5l2.5 0 1 3.5-1.8 1.3a8 8 0 0 0 4.5 4.5L11 9l3.5 1v2.5c0 1-1 2-2 2C6.5 14.5 1.5 9.5 1.5 3.5c0-1 1-2 2-2z"/></svg>
          <span>+0212 0555 204 718</span>
        </li>
        <li>
          <svg viewBox="0 0 16 16"><rect x="1" y="3" width="14" height="10" fill="#2b3586"/><path d="M1.5 3.5L8 9l6.5-5.5" stroke="#ebebeb" stroke-width="1.3" fill="none"/></svg>
          <span>n.verel@harborline.ma</span>
        </li>
        <li class="web">
          <svg viewBox="0 0 16 16"><circle cx="8" cy="8" r="6.5" fill="#2b3586"/><path d="M1.5 8h13M8 1.5c-3 3.5-3 9.5 0 13M8 1.5c3 3.5 3 9.5 0 13" stroke="#ebebeb" stroke-width="1" fill="none"/></svg>
          <span>www.<span class="accent">harborline</span>.ma</span>
        </li>
      </ul>
      <p class="address">PO BOX 50817 Calder<br>Larkfield, AB T2K-4P</p>
    </div>
    <div class="front-stripe"><span class="navy"></span><span class="orange"></span></div>
  </section>

  <section class="card card-back">
    <div class="back-brand">
      <div class="back-dot"></div>
      <p class="back-name">HARBORLINE</p>
      <p class="back-sub">CLINICS</p>
    </div>
    <div class="back-stripe orange"></div>
    <div class="back-stripe sky"></div>
  </section>
</body>
</html>
```